Restyle corporate identity (+ logo) for a road construction company

We need a new logo and stationary design for our company VARNOK path. VARNOK path® increases the road base strength, while reducing major costs and time of road construction. Attached some examples of the current design.

Our wishes for the new logo:
- Business look
- Style sheet
- Modern

More information: www.varnokpath.example
Updates

Target Market(s)

Government

Industry/Entity Type

Construction

Requirements
Must have
• Logo (with road sign) + text

```html
<!DOCTYPE html>
<html lang="en">
<head>
<meta charset="utf-8">
<title>VARNOK path – Business Card</title>
<link rel="stylesheet" href="https://fonts.googleapis.com/css2?family=Source+Sans+3:wght@400;600;700&display=swap">
<style>
  :root {
    --backdrop: #8f9091;
    --card-white: #eeeff0;
    --brand-blue: #0a78dc;
    --road-grey-dark: #8a8b8d;
    --road-grey-light: #e6e7e9;
    --text-light: #eaf3fc;
  }
  * { margin: 0; padding: 0; box-sizing: border-box; }
  html, body {
    width: 1105px;
    height: 1200px;
    overflow: hidden;
    background: var(--backdrop);
    font-family: "Source Sans 3", Arial, sans-serif;
  }
  .card {
    position: absolute;
    left: 182px;
    width: 747px;
    height: 426px;
    overflow: hidden;
  }
  .card-front { top: 119px; background: var(--brand-blue); }
  .card-back { top: 637px; background: var(--card-white); }

  .front-graphic {
    position: absolute;
    left: 0; top: 0;
    width: 747px; height: 426px;
  }
  .edge-tab {
    position: absolute;
    right: 0; top: 58px;
    width: 16px; height: 52px;
    background: var(--card-white);
  }
  .contact-block {
    position: absolute;
    right: 46px;
    text-align: right;
    color: var(--text-light);
  }
  .identity { top: 54px; }
  .holder-name {
    font-size: 26px;
    font-weight: 600;
    letter-spacing: 0.3px;
    line-height: 32px;
  }
  .holder-role {
    font-size: 19px;
    line-height: 24px;
  }
  .address {
    top: 209px;
    font-size: 19px;
    line-height: 26.5px;
  }
  .channels {
    top: 301px;
    right: 44px;
    font-size: 19px;
    line-height: 29px;
  }
  .channel {
    display: flex;
    justify-content: flex-end;
    align-items: center;
    gap: 6px;
  }
  .channel svg { width: 17px; height: 17px; flex: none; }

  .wordmark {
    position: absolute;
    left: 0; right: 0;
    top: 180px;
    text-align: center;
    font-size: 50px;
    font-weight: 600;
    color: var(--brand-blue);
    letter-spacing: 1px;
    line-height: 60px;
  }
</style>
</head>
<body>
  <section class="card card-front">
    <svg class="front-graphic" viewBox="0 0 747 426" role="img" aria-label="Road graphic of the brand">
      <defs>
        <linearGradient id="roadTone" x1="0" y1="0" x2="1" y2="0">
          <stop offset="0" stop-color="var(--road-grey-dark)"/>
          <stop offset="0.45" stop-color="var(--road-grey-light)"/>
          <stop offset="1" stop-color="var(--road-grey-light)"/>
        </linearGradient>
      </defs>
      <polygon points="0,0 294,0 384,426 0,426" fill="url(#roadTone)"/>
    </svg>
    <div class="edge-tab"></div>

    <div class="contact-block identity">
      <p class="holder-name">MAREN DOLVIK</p>
      <p class="holder-role">CEO/Founder</p>
    </div>

    <div class="contact-block address">
      <p>Lindenkade 57</p>
      <p>4811 ZX Veldhaven</p>
      <p>The Netherlands</p>
    </div>

    <div class="contact-block channels">
      <p class="channel">612 904 7315
        <svg viewBox="0 0 24 24" aria-hidden="true"><path fill="currentColor" d="M6.6 10.8a15.1 15.1 0 0 0 6.6 6.6l2.2-2.2a1 1 0 0 1 1-.25 11.4 11.4 0 0 0 3.6.57 1 1 0 0 1 1 1V20a1 1 0 0 1-1 1A17 17 0 0 1 3 4a1 1 0 0 1 1-1h3.5a1 1 0 0 1 1 1c0 1.25.2 2.45.57 3.6a1 1 0 0 1-.25 1z"/></svg>
      </p>
      <p class="channel">info@varnokpath.example
        <svg viewBox="0 0 24 24" aria-hidden="true"><path fill="currentColor" d="M3 5h18v14H3z M3 5l9 7 9-7" stroke="var(--brand-blue)" stroke-width="1.5"/></svg>
      </p>
      <p class="channel">www.varnokpath.example
        <svg viewBox="0 0 24 24" aria-hidden="true"><circle cx="12" cy="12" r="10" fill="currentColor"/><path d="M2 12h20M12 2c3 3 3 17 0 20M12 2c-3 3-3 17 0 20" stroke="var(--brand-blue)" stroke-width="1.3" fill="none"/></svg>
      </p>
    </div>
  </section>

  <section class="card card-back">
    <p class="wordmark">VARNOK path</p>
  </section>
</body>
</html>
```